Business Card Design

New business card design

Target Market(s)

Residential & Commercial Property Managers

Industry/Entity Type

Plumbing Services

Contact Information for Business Card

Name - Rowan Keddle, title - Director, Phone Number - 0431 286 517, email - rowan@tbk-plumbing.com.au, Company ABN - 73 215 904 386,

Font styles to use
Sans Serif

Colors
0054AA
0677BA
7BADD7
CADEEF
E8F1F8

```html
<!DOCTYPE html>
<html lang="en">
<head>
<meta charset="utf-8">
<title>TBK Plumbing Services – Business Card</title>
<link href="https://fonts.googleapis.com/css2?family=Roboto:wght@300;400;500;700&display=swap" rel="stylesheet">
<style>
  :root {
    --page-bg: #d9d4cf;
    --card-bg: #f3f5f7;
    --band: #6e655e;
    --ink-dark: #2a2a2c;
    --ink-light: #ffffff;
    --ink-soft: #e6e1dc;
    --accent: #0677ba;
    --accent-light: #1a9ad6;
    --accent-deep: #0a6f9c;
  }
  * { margin: 0; padding: 0; box-sizing: border-box; }
  html, body {
    width: 1200px;
    height: 1054px;
    overflow: hidden;
    background: var(--page-bg);
    font-family: "Roboto", sans-serif;
  }
  .card {
    position: absolute;
    left: 100px;
    top: 224px;
    width: 1000px;
    height: 605px;
    background: var(--card-bg);
    border-radius: 24px;
    overflow: hidden;
    box-shadow: 0 10px 30px rgba(0,0,0,0.12);
  }
  .brand {
    position: absolute;
    left: 60px;
    top: 96px;
    display: flex;
    align-items: center;
    gap: 16px;
  }
  .brand-dot {
    width: 24px;
    height: 24px;
    border-radius: 50%;
    background: var(--accent);
  }
  .brand-name {
    font-size: 46px;
    font-weight: 500;
    line-height: 1;
    color: var(--ink-dark);
  }
  .band-left {
    position: absolute;
    left: 0;
    top: 257px;
    width: 572px;
    height: 243px;
    background: var(--band);
  }
  .band-right {
    position: absolute;
    left: 916px;
    top: 257px;
    width: 84px;
    height: 243px;
    background: var(--band);
  }
  .feature-graphic {
    position: absolute;
    left: 592px;
    top: 86px;
    width: 304px;
    height: 490px;
    border-radius: 150px 150px 152px 152px;
    background: linear-gradient(160deg, var(--accent-light) 0%, var(--accent) 55%, var(--accent-deep) 100%);
  }
  .person-name {
    position: absolute;
    left: 60px;
    top: 24px;
    font-size: 40px;
    font-weight: 500;
    line-height: 1.2;
    color: var(--ink-light);
  }
  .person-title {
    position: absolute;
    left: 60px;
    top: 72px;
    font-size: 25px;
    font-weight: 300;
    line-height: 1.2;
    color: var(--ink-soft);
  }
  .contact-list {
    position: absolute;
    left: 62px;
    top: 110px;
    list-style: none;
  }
  .contact-item {
    display: flex;
    align-items: center;
    height: 35px;
    font-size: 25px;
    font-weight: 300;
    color: var(--ink-light);
    white-space: nowrap;
  }
  .contact-icon {
    width: 22px;
    height: 22px;
    margin-right: 20px;
    fill: var(--ink-soft);
  }
  .address {
    position: absolute;
    left: 60px;
    top: 530px;
    font-size: 24px;
    font-weight: 400;
    color: var(--ink-dark);
  }
</style>
</head>
<body>
  <div class="card">
    <div class="brand">
      <span class="brand-dot"></span>
      <span class="brand-name">TBK Plumbing Services</span>
    </div>

    <div class="band-right"></div>
    <div class="feature-graphic" role="img" aria-label="Large blue water drop graphic"></div>

    <div class="band-left">
      <div class="person-name">Rowan Keddle</div>
      <div class="person-title">Director</div>
      <ul class="contact-list">
        <li class="contact-item">
          <svg class="contact-icon" viewBox="0 0 24 24" aria-hidden="true">
            <path d="M6.6 10.8a15.1 15.1 0 0 0 6.6 6.6l2.2-2.2a1 1 0 0 1 1-.25 11.4 11.4 0 0 0 3.6.6 1 1 0 0 1 1 1V20a1 1 0 0 1-1 1A17 17 0 0 1 3 4a1 1 0 0 1 1-1h3.5a1 1 0 0 1 1 1c0 1.25.2 2.45.6 3.6a1 1 0 0 1-.25 1z"/>
          </svg>
          0431 286 517
        </li>
        <li class="contact-item">
          <svg class="contact-icon" viewBox="0 0 24 24" aria-hidden="true">
            <path d="M2 5h20v14H2z M4 7v.4l8 5.2 8-5.2V7z" fill-rule="evenodd"/>
          </svg>
          rowan@tbk-plumbing.com.au
        </li>
        <li class="contact-item">
          <svg class="contact-icon" viewBox="0 0 24 24" aria-hidden="true">
            <path d="M12 2a10 10 0 1 0 0 20 10 10 0 0 0 0-20zm6.9 6h-2.9a15.6 15.6 0 0 0-1.4-3.6A8 8 0 0 1 18.9 8zM12 4c.8 1.2 1.5 2.5 1.9 4h-3.8c.4-1.5 1.1-2.8 1.9-4zM4.3 14a8 8 0 0 1 0-4h3.4a16 16 0 0 0 0 4zm.8 2h2.9c.3 1.3.8 2.5 1.4 3.6A8 8 0 0 1 5.1 16zM8 8H5.1a8 8 0 0 1 4.3-3.6C8.8 5.5 8.3 6.7 8 8zm4 12c-.8-1.2-1.5-2.5-1.9-4h3.8c-.4 1.5-1.1 2.8-1.9 4zm2.3-6H9.7a14.7 14.7 0 0 1 0-4h4.6a14.7 14.7 0 0 1 0 4zm.3 5.6c.6-1.1 1.1-2.3 1.4-3.6h2.9a8 8 0 0 1-4.3 3.6zm1.7-5.6a16 16 0 0 0 0-4h3.4a8 8 0 0 1 0 4z"/>
          </svg>
          ABN 73 215 904 386
        </li>
      </ul>
    </div>

    <div class="address">12 Harbour Rd, Brookvale NSW 2100</div>
  </div>
</body>
</html>
```